Refresh of graphic design for existing website

We would like to refresh our website. Please see the attached design specifications.

Industry/Entity Type

Graphic Design

```html
<!DOCTYPE html>
<html lang="en">
<head>
<meta charset="utf-8">
<title>Northgate Tool Council</title>
<link href="https://fonts.googleapis.com/css2?family=Open+Sans:wght@400;600;700&family=PT+Serif:ital,wght@0,400;0,700;1,400&display=swap" rel="stylesheet">
<style>
:root{
  --ink:#2b2b2b;
  --muted:#6b6b6b;
  --blue:#1b8fd2;
  --blue-dark:#1478b3;
  --navy:#1d2936;
  --navy-2:#27384a;
  --topbar:#1a1f25;
  --header:#eef0f2;
  --page:#ffffff;
  --footer:#262626;
  --footer-2:#1c1c1c;
  --footer-text:#8f8f8f;
  --rule:#d9dcdf;
}
*{box-sizing:border-box;margin:0;padding:0}
html,body{width:692px;height:1200px;overflow:hidden}
body{background:var(--page);font-family:"PT Serif",Georgia,serif;color:var(--ink);position:relative}
.sans{font-family:"Open Sans",Arial,sans-serif}

/* top bar */
.topbar{height:26px;background:var(--topbar);display:flex;align-items:center;padding:0 18px;gap:7px}
.topbar .dot{width:12px;height:12px;border-radius:50%;background:#3d4752}
.topbar .search{margin-left:auto;width:120px;height:14px;border-radius:7px;background:#2f363e}

/* header */
.header{height:88px;background:var(--header);position:relative;border-bottom:1px solid var(--rule)}
.brand{position:absolute;left:18px;top:14px;display:flex;align-items:center;gap:8px}
.brand-mark{width:40px;height:40px;border-radius:50%;background:var(--blue)}
.brand-name{font-family:"Open Sans",Arial,sans-serif;font-weight:700;font-size:19px;color:var(--navy);line-height:1.1}
.login{position:absolute;right:18px;top:36px;display:flex;gap:6px}
.login .field{width:122px;height:22px;background:#fff;border:1px solid #c9cdd2;font-family:"Open Sans",Arial,sans-serif;font-size:9px;color:#888;padding:4px 6px}
.login .btn{width:64px;height:22px;background:var(--navy);color:#fff;font-family:"Open Sans",Arial,sans-serif;font-size:9px;font-weight:600;text-align:center;line-height:22px}
.nav{position:absolute;left:240px;right:18px;top:70px;display:flex;justify-content:space-between;font-family:"Open Sans",Arial,sans-serif;font-size:8.5px;font-weight:600;color:#5a6470;letter-spacing:.3px}
.nav .active{color:var(--blue)}

/* hero */
.hero{position:absolute;top:143px;left:0;width:692px;height:330px;background:var(--navy)}
.slider{position:absolute;left:18px;top:14px;width:646px;height:304px;overflow:hidden}
.slide-photo{position:absolute;inset:0;background:linear-gradient(110deg,#5a6572 0%,#8a939c 35%,#c9ccd0 60%,#9aa3ab 100%)}
.slide-caption{position:absolute;left:0;top:0;width:202px;height:100%;background:rgba(36,52,68,.82);padding:54px 14px 0 14px;color:#e7ecf1}
.slide-caption h2{font-size:15px;font-weight:400;margin-bottom:10px}
.slide-caption p{font-size:9px;line-height:1.55;color:#c6d0da}
.slide-caption .more{position:absolute;right:14px;bottom:20px;font-size:9px;color:#e7ecf1}

/* quote */
.quote{position:absolute;top:498px;left:0;width:692px;height:64px}
.quote p{position:absolute;left:88px;right:88px;top:8px;text-align:center;font-style:italic;font-size:14px;line-height:1.45;color:#33414f}
.quote svg{position:absolute;top:14px}
.quote-rule{position:absolute;top:590px;left:18px;right:18px;height:1px;background:var(--rule)}

/* columns */
.cols{position:absolute;top:606px;left:18px;right:18px;display:flex;gap:22px}
.col{flex:1}
.col h3{font-size:11px;font-weight:700;color:var(--ink);margin-bottom:9px}
.col .thumb{height:122px;margin-bottom:10px}
.col p{font-size:8.5px;line-height:1.55;color:var(--muted)}
.col .more{display:block;margin-top:10px;font-family:"Open Sans",Arial,sans-serif;font-size:8.5px;font-weight:700;color:var(--blue-dark)}
.event{display:flex;gap:8px;margin-bottom:6px}
.event .ethumb{width:32px;height:30px;flex:none}
.event p{font-size:8px}
.event-more{text-align:right;margin-bottom:24px!important}

/* footer */
.footer{position:absolute;top:878px;left:0;width:692px;height:322px;background:var(--footer);color:var(--footer-text)}
.fcols{position:absolute;left:18px;right:18px;top:18px;display:flex;gap:18px}
.fcol{flex:1}
.fcol h4{font-family:"Open Sans",Arial,sans-serif;font-size:8px;font-weight:700;color:#e0e0e0;letter-spacing:.4px;margin-bottom:12px}
.fcol p{font-size:7.5px;line-height:1.6;margin-bottom:8px}
.post{display:flex;gap:7px;margin-bottom:12px}
.post .pthumb{width:22px;height:22px;flex:none;background:linear-gradient(135deg,#4a4f55,#7b8087)}
.post p{font-size:7px;line-height:1.5;margin:0}
.links{list-style:none}
.links li{font-size:7.5px;line-height:1;margin-bottom:9px;display:flex;align-items:center;gap:6px}
.links li::before{content:"";width:3px;height:3px;background:var(--blue);flex:none}
.cfield{height:18px;background:#333;border:1px solid #3d3d3d;margin-bottom:8px;font-family:"Open Sans",Arial,sans-serif;font-size:7.5px;color:#8a8a8a;padding:3px 6px}
.cfield.tall{height:44px}
.cbtn{width:50px;height:18px;background:var(--blue);color:#fff;font-family:"Open Sans",Arial,sans-serif;font-size:7.5px;font-weight:700;text-align:center;line-height:18px;margin-top:18px}
.copyright{position:absolute;left:0;bottom:0;width:100%;height:36px;background:var(--footer-2);padding:14px 18px;font-size:7px;color:#6f6f6f}
</style>
</head>
<body>

<div class="topbar">
  <span class="dot"></span><span class="dot"></span><span class="dot"></span><span class="dot"></span><span class="dot"></span>
  <span class="search"></span>
</div>

<header class="header">
  <div class="brand">
    <span class="brand-mark"></span>
    <span class="brand-name">Northgate Tool Council</span>
  </div>
  <div class="login">
    <div class="field">Username</div>
    <div class="field">Password</div>
    <div class="btn">Login</div>
  </div>
  <nav class="nav">
    <span class="active">HOME</span><span>ABOUT US</span><span>WORKSHOP</span><span>NTC MEMBERS</span><span>NTC EVENTS</span><span>TEK</span><span>MY LIBRARY</span>
  </nav>
</header>

<section class="hero">
  <div class="slider">
    <div class="slide-photo" role="img" aria-label="Mechanic in blue overalls holding a cloth in a car workshop"></div>
    <div class="slide-caption">
      <h2>Aliquatjusto quisque</h2>
      <p>Lorem ipsum dolor sit amet, consectetur adipiscing elit. Mauris et tristique sem. Nunc nec ipsum sed nisi dictum mollis. Praesent malesuada mauris a odio adipiscing mollis. In varius tincidunt elit vitae eleifend. Etiam consectetur suscipit est et aliquet. Quisque malesuada lacus.</p>
      <span class="more">Read More</span>
    </div>
  </div>
</section>

<section class="quote">
  <svg style="left:30px" width="14" height="26" viewBox="0 0 14 26"><path d="M12 2 L3 13 L12 24" fill="none" stroke="#33414f" stroke-width="3.5"/></svg>
  <p>“ Lorem ipsum dolor sit amet, consectetur adipiscing elit. Nunc non diam erat. In fringilla massa ut nisi ullamcorper pellentesque „</p>
  <svg style="right:30px" width="14" height="26" viewBox="0 0 14 26"><path d="M2 2 L11 13 L2 24" fill="none" stroke="#33414f" stroke-width="3.5"/></svg>
</section>
<div class="quote-rule"></div>

<section class="cols">
  <article class="col">
    <h3>Breaking News</h3>
    <div class="thumb" role="img" aria-label="Hand holding a wrench over engine parts" style="background:linear-gradient(135deg,#3e5f8a,#8aa4c2 60%,#d0d6dc)"></div>
    <p>Lorem ipsum dolor sit amet, consectetur adipiscing elit. Nunc non diam erat. In fringilla massa ut nisi ullamcorper pellentesque.</p>
    <span class="more">Continue Reading »</span>
  </article>
  <article class="col">
    <h3>Join NTC</h3>
    <div class="thumb" role="img" aria-label="Two technicians reviewing a laptop in a garage" style="background:linear-gradient(135deg,#6b7784,#b9c2cb 55%,#3d7fb5)"></div>
    <p>Lorem ipsum dolor sit amet, consectetur adipiscing elit. Nunc non diam erat. In fringilla massa ut nisi ullamcorper pellentesque.</p>
    <span class="more">Continue Reading »</span>
  </article>
  <article class="col">
    <h3>Industrial Events</h3>
    <div class="event">
      <div class="ethumb" role="img" aria-label="Event photo" style="background:linear-gradient(135deg,#4d5966,#9aa5b0)"></div>
      <p>Lorem ipsum dolor sit amet, consectetur adipiscing elit. Nunc non diam erat. In fringilla massa ut nisi ullamcorper.</p>
    </div>
    <span class="more event-more">Continue Reading »</span>
    <div class="event">
      <div class="ethumb" role="img" aria-label="Event photo" style="background:linear-gradient(135deg,#5a5f66,#a7acb2)"></div>
      <p>Lorem ipsum dolor sit amet, consectetur adipiscing elit. Nunc non diam erat. In fringilla massa ut nisi ullamcorper.</p>
    </div>
    <span class="more" style="text-align:right">Continue Reading »</span>
  </article>
</section>

<footer class="footer">
  <div class="fcols">
    <div class="fcol">
      <h4>COMPANY DETAILS</h4>
      <p>Lorem ipsum dolor sit amet, consectetur adipiscing elit. Nunc non diam erat. In fringilla massa ut nisi.</p>
      <p>Northgate Tool Council<br>1420 Harbor Lane, Suite 8<br>Dayton, OH 45402<br>Tel: 555-014-2290<br>Fax: 555-014-2291</p>
      <p>info@northgatetool.org<br>www.northgatetool.org</p>
    </div>
    <div class="fcol">
      <h4>LATEST BLOG POSTS</h4>
      <div class="post"><div class="pthumb" role="img" aria-label="Blog post thumbnail"></div><p>Lorem ipsum dolor sit amet, consectetur adipiscing elit. Nunc non diam erat.</p></div>
      <div class="post"><div class="pthumb" role="img" aria-label="Blog post thumbnail"></div><p>Lorem ipsum dolor sit amet, consectetur adipiscing elit. Nunc non diam erat.</p></div>
      <div class="post"><div class="pthumb" role="img" aria-label="Blog post thumbnail"></div><p>Lorem ipsum dolor sit amet, consectetur adipiscing elit. Nunc non diam erat.</p></div>
    </div>
    <div class="fcol">
      <h4>QUICK LINKS</h4>
      <ul class="links">
        <li>Lorem ipsum dolor</li>
        <li>Sed consectetur</li>
        <li>Praesent vel nisi</li>
        <li>Curabitur tincidunt</li>
        <li>Aliquam eget erat</li>
        <li>Vivamus at lacus</li>
        <li>In nec justo</li>
        <li>Tristique mollis</li>
      </ul>
    </div>
    <div class="fcol">
      <h4>CONTACT US</h4>
      <div class="cfield">Name</div>
      <div class="cfield">Email</div>
      <div class="cfield tall">Message</div>
      <div class="cbtn">SUBMIT</div>
    </div>
  </div>
  <div class="copyright">Copyright © 2013 Northgate Tool Council – All Rights Reserved</div>
</footer>

</body>
</html>
```